Corvel Capital LLC

Need Professional Business cards for New Investment Fund

Target Market(s)

High Quality investors

Industry/Entity Type

Financial

Contact Information for Business Card

Phone Number +1 555 284 6190
Name Lukas Varenko
Title Fund Manager
email lv@FundCorvel.com
Website www.FundCorvel.com

Colors

Designer to choose colors to be used in the design.

Requirements
Must have
• Must have our Logo and all of the above. Must be made so lettering and loge can be raised

```html
<!DOCTYPE html>
<html lang="en">
<head>
<meta charset="utf-8">
<title>Quillmere – Business Card</title>
<link href="https://fonts.googleapis.com/css2?family=Lato:wght@400;700&display=swap" rel="stylesheet">
<style>
  :root {
    --backdrop: #2f3130;
    --card-dark: #444c40;
    --card-light: #f3f3f3;
    --accent: #1fe01a;
    --ink: #3f4a3c;
    --emboss: #3b4237;
  }
  * { margin: 0; padding: 0; box-sizing: border-box; }
  html, body { width: 1200px; height: 1015px; overflow: hidden; }
  body {
    background: var(--backdrop);
    font-family: "Lato", sans-serif;
    position: relative;
  }
  .card {
    position: absolute;
    left: 220px;
    width: 760px;
    height: 430px;
    border-bottom: 12px solid var(--accent);
    box-shadow: 0 14px 30px rgba(0,0,0,0.45);
  }
  .card-back { top: 55px; background: var(--card-dark); }
  .card-front { top: 530px; background: var(--card-light); }

  .back-wordmark {
    position: absolute;
    left: 0; right: 0; top: 165px;
    text-align: center;
    font-size: 52px;
    font-weight: 700;
    letter-spacing: 5px;
    color: var(--emboss);
  }

  .front-wordmark {
    position: absolute;
    left: 60px; top: 195px;
    display: flex; align-items: center; gap: 12px;
    font-size: 36px; font-weight: 700; letter-spacing: 2px;
    color: var(--ink);
  }
  .front-wordmark .mark-dot {
    width: 20px; height: 20px; background: var(--accent); flex: none;
  }

  .identity {
    position: absolute;
    left: 400px; top: 120px;
    padding-left: 22px;
    border-left: 3px solid var(--accent);
  }
  .identity .name {
    font-size: 27px; font-weight: 700; letter-spacing: 0.5px;
    color: var(--ink); text-transform: uppercase;
  }
  .identity .name .first { color: var(--accent); }
  .identity .title { font-size: 19px; color: var(--ink); margin-top: 2px; }

  .contacts {
    position: absolute;
    left: 400px; top: 205px;
    padding-left: 22px;
    border-left: 3px solid var(--ink);
    list-style: none;
  }
  .contacts li {
    display: flex; align-items: center; gap: 10px;
    font-size: 19px; color: var(--ink); line-height: 30px;
  }
  .contacts svg { width: 16px; height: 16px; fill: var(--accent); flex: none; }
</style>
</head>
<body>
  <section class="card card-back" aria-label="Card back">
    <div class="back-wordmark">QUILLMERE</div>
  </section>

  <section class="card card-front" aria-label="Card front">
    <div class="front-wordmark"><span class="mark-dot"></span>QUILLMERE</div>

    <div class="identity">
      <div class="name"><span class="first">Lukas</span> Varenko</div>
      <div class="title">Fund Manager</div>
    </div>

    <ul class="contacts">
      <li>
        <svg viewBox="0 0 16 16"><path d="M3 1h3l1.5 4-2 1.2a9 9 0 0 0 4.3 4.3L11 8.5 15 10v3a2 2 0 0 1-2 2A12 12 0 0 1 1 3a2 2 0 0 1 2-2z"/></svg>
        +1 555 284 6190
      </li>
      <li>
        <svg viewBox="0 0 16 16"><path d="M1 3h14v10H1z M1 3l7 6 7-6" stroke="#f3f3f3" stroke-width="1.2"/></svg>
        lv@FundCorvel.com
      </li>
      <li>
        <svg viewBox="0 0 16 16"><circle cx="8" cy="8" r="7"/><path d="M1 8h14M8 1c3 3 3 11 0 14M8 1c-3 3-3 11 0 14" stroke="#f3f3f3" stroke-width="1" fill="none"/></svg>
        www.FundCorvel.com
      </li>
    </ul>
  </section>
</body>
</html>
```